Charity Initiative needs a WebPage design

We need a web design for charity initiative by two young guys riding their bikes around Australia to support HarbourLight which helps people with depression and anxiety. Full brief and requirements are attached in the PDF and word document. We have the logo already done and attached. Website will be done in Wordpress and need to get Donations, display current donations, show live Video feed, GPS tracker, Blogs etc and also ability to sell merchandise later

Target Market(s)

Sponsors, Business, Young People

Number of Pages Required

4 page

Font styles to use
Serif
Sans Serif
Decorative
Script

Requirements
Must have
• As per Brief and also Donation status etc
Nice to have
• Please check my logo and read the Bried

```html
<!DOCTYPE html>
<html lang="en">
<head>
<meta charset="utf-8">
<title>Coastline Ride – The Motorcycle Adventure Around Australia</title>
<link rel="stylesheet" href="https://fonts.googleapis.com/css2?family=Roboto+Condensed:wght@400;700&family=Roboto:wght@400;500;700&family=Rubik+Dirt&display=swap">
<style>
:root{
  --pink:#e8246a;
  --pink-deep:#c81e5c;
  --teal:#3bb3a6;
  --teal-dark:#2a9a8e;
  --black:#0d0d0d;
  --white:#ffffff;
  --ink:#222222;
  --grey:#555555;
  --navy:#1e1d5c;
  --map:#ece9e2;
}
*{margin:0;padding:0;box-sizing:border-box}
html,body{width:1200px;height:2525px;overflow:hidden}
body{position:relative;background:var(--navy);font-family:"Roboto",Arial,sans-serif;color:var(--ink)}
.backdrop{position:absolute;left:0;top:0;width:1200px;height:620px;
  background:linear-gradient(180deg,#0c1230 0%,#16306a 45%,#1f2a6b 75%,var(--navy) 100%)}
.page{position:absolute;left:162px;top:0;width:876px;height:2525px;background:var(--white)}

/* header */
.site-header{position:relative;height:182px;background:var(--white)}
.brand{position:absolute;left:26px;top:42px;display:flex;align-items:center;gap:14px}
.brand-dot{width:60px;height:60px;border-radius:50%;background:var(--pink)}
.brand-name{font-family:"Roboto Condensed",sans-serif;font-weight:700;font-size:46px;color:var(--pink);line-height:1}
.btn-donate-top{position:absolute;left:651px;top:64px;width:180px;height:54px;background:var(--pink);color:var(--white);
  font-family:"Roboto Condensed",sans-serif;font-weight:700;font-size:24px;text-transform:uppercase;display:flex;align-items:center;justify-content:center}

.main-nav{height:44px;background:var(--black);display:flex;align-items:center;padding-left:30px}
.main-nav a{color:var(--white);text-decoration:none;font-family:"Roboto Condensed",sans-serif;font-size:18px;margin-right:38px}
.main-nav a.active{background:var(--teal);padding:3px 8px;margin-left:-8px;margin-right:30px}
.social{margin-left:auto;margin-right:26px;display:flex;gap:8px}
.social span{width:26px;height:26px;border:1.5px solid var(--white);border-radius:3px;display:flex;align-items:center;justify-content:center}
.social span i{width:8px;height:8px;background:var(--white);border-radius:50%}

/* hero */
.hero{position:relative;height:447px;background:var(--pink)}
.hero-video{position:absolute;left:28px;top:35px;width:384px;height:256px;border:4px solid var(--black);
  background:linear-gradient(160deg,#4f7d3a,#2f4f25 55%,#8a8a8a)}
.play{position:absolute;left:50%;top:50%;transform:translate(-50%,-50%)}
.hero-title{position:absolute;left:437px;top:22px;font-family:"Rubik Dirt",cursive;font-size:31px;line-height:38px;color:var(--white);text-transform:uppercase}
.stats{position:absolute;left:427px;top:136px;width:421px;height:135px;background:var(--black);display:flex;align-items:center}
.stat{flex:1;text-align:center;border-right:1px solid #444}
.stat:last-child{border-right:0}
.stat-label{color:var(--white);font-size:22px;font-family:"Roboto",sans-serif}
.stat-value{color:var(--pink);font-family:"Roboto Condensed",sans-serif;font-weight:700;font-size:30px;margin-top:12px}
.hero-cause{position:absolute;left:0;width:100%;top:300px;text-align:center;font-family:"Rubik Dirt",cursive;font-size:30px;color:var(--white);text-transform:uppercase}
.hero-sub{position:absolute;left:0;width:100%;top:338px;text-align:center;font-size:28px;color:var(--black)}
.btn-teal{background:var(--teal);color:var(--white);font-size:21px;display:flex;align-items:center;justify-content:center}
.hero .btn-teal{position:absolute;left:360px;top:387px;width:173px;height:42px}

/* section headings */
.section-title{font-family:"Roboto Condensed",sans-serif;font-weight:700;font-size:42px;text-align:center}
.section-title .accent{color:var(--pink)}
.rule{width:88px;height:3px;background:var(--black);margin:10px auto 0}

.location{height:105px;padding-top:18px}
.location .section-title{color:var(--teal)}
.map{height:346px;background:var(--map);position:relative}

.funds{position:relative;height:448px;background:linear-gradient(180deg,#8ecfc9 0%,#b6e2dd 40%,#3c6a5a 68%,#2b3a2e 80%,#3a3a3a 100%)}
.funds .section-title{position:absolute;top:38px;width:100%;color:var(--black)}
.funds .rule{position:absolute;top:100px;left:394px;margin:0}
.tag{position:absolute;font-family:"Roboto Condensed",sans-serif;font-weight:700;text-align:center}
.tag small{display:block;font-size:13px;color:var(--black);margin-bottom:4px}
.tag b{display:inline-block;background:var(--black);color:var(--pink);padding:6px 10px;border-radius:4px;font-size:15px}
.tag.big b{font-size:22px;padding:10px 16px}
.track{position:absolute;left:50px;top:217px;width:778px;height:52px;background:var(--black)}
.track-done{position:absolute;left:0;top:0;width:200px;height:52px;background:var(--pink-deep)}
.funds .btn-pink{position:absolute;left:351px;top:307px;width:175px;height:54px;background:var(--pink);color:var(--white);font-size:22px;display:flex;align-items:center;justify-content:center}

/* journals */
.journals{position:relative;height:422px;background:linear-gradient(180deg,#d62e68 0%,#c2205a 60%,#e0416f 100%)}
.journals .section-title{position:absolute;top:26px;width:100%;color:var(--white)}
.journals .rule{position:absolute;top:82px;left:394px;margin:0;background:var(--black)}
.journal{position:absolute;top:116px;width:342px;color:var(--white)}
.journal-photo{position:relative;height:125px;border:2px solid #ddd;background:linear-gradient(180deg,#6f7e86,#3b4044)}
.date{position:absolute;left:0;top:0;width:38px;height:46px;background:var(--black);text-align:center;font-family:"Roboto Condensed",sans-serif;font-weight:700;color:var(--white);line-height:1}
.date b{display:block;font-size:22px;padding-top:3px}
.date span{font-size:9px}
.count{text-align:right;font-size:11px;margin-top:6px}
.journal h3{font-size:14px;font-weight:700;margin-top:2px}
.journal p{font-size:13px;line-height:18px;margin-top:2px}
.btn-black{display:inline-flex;align-items:center;justify-content:center;background:var(--black);color:var(--white);font-size:12px;font-weight:500;width:100px;height:30px}
.journal .btn-black{margin-top:10px}

/* team */
.team{position:relative;height:399px}
.member{position:absolute;top:55px;width:250px;text-align:center}
.avatar{width:136px;height:136px;border-radius:50%;margin:0 auto;background:linear-gradient(160deg,#b79a86,#6d584b)}
.avatar.partner{background:#efefef;display:flex;align-items:center;justify-content:center}
.avatar.partner span{font-family:"Roboto",sans-serif;font-size:15px;color:var(--teal);font-weight:500}
.member h4{font-size:25px;font-weight:500;margin-top:12px;color:var(--ink)}
.member p{font-size:12px;line-height:18px;color:var(--grey);margin:8px auto 0;width:220px}
.member .btn-black{margin-top:16px}

.newsletter{height:88px;background:var(--teal);display:flex;align-items:center;padding-left:66px;color:var(--white);font-size:15px}
.newsletter .field{width:298px;height:34px;border:1px solid var(--white);margin-left:14px;font-size:12px;display:flex;align-items:center;padding-left:12px}
.newsletter .subscribe{width:106px;height:34px;border:1px solid var(--white);margin-left:12px;font-size:13px;font-weight:700;display:flex;align-items:center;justify-content:center}

.site-footer{height:44px;background:var(--black);color:var(--white);display:flex;align-items:center;padding:0 16px 0 24px;font-size:12px;font-weight:700}
.payments{margin-left:auto;display:flex;align-items:center;gap:6px}
.payments em{font-style:normal;margin-right:6px}
.card{width:42px;height:24px;background:var(--white);color:var(--ink);border-radius:3px;font-size:8px;display:flex;align-items:center;justify-content:center}
</style>
</head>
<body>
<div class="backdrop" role="img" aria-label="Night city skyline along a river behind the page"></div>

<div class="page">
  <header class="site-header">
    <div class="brand"><span class="brand-dot"></span><span class="brand-name">Coastline Ride</span></div>
    <a class="btn-donate-top">Donate Now</a>
  </header>

  <nav class="main-nav">
    <a class="active">Home</a><a>Journal</a><a>Riders</a><a>Riders</a><a>Contact Us</a>
    <div class="social" aria-label="Social links"><span><i></i></span><span><i></i></span><span><i></i></span><span><i></i></span><span><i></i></span></div>
  </nav>

  <section class="hero">
    <div class="hero-video" role="img" aria-label="Live video of two riders cornering on motorcycles">
      <svg class="play" width="96" height="96" viewBox="0 0 96 96"><circle cx="48" cy="48" r="44" fill="none" stroke="#e8246a" stroke-width="7"/><circle cx="48" cy="48" r="34" fill="#e8246a"/><path d="M40 32 L64 48 L40 64 Z" fill="#fff"/></svg>
    </div>
    <h1 class="hero-title">The Motorcycle Adventure<br>Around Australia</h1>
    <div class="stats">
      <div class="stat"><div class="stat-label">Days</div><div class="stat-value">50</div></div>
      <div class="stat"><div class="stat-label">Kilometers</div><div class="stat-value">10,568</div></div>
      <div class="stat"><div class="stat-label">Provinces</div><div class="stat-value">33</div></div>
    </div>
    <p class="hero-cause">We Helps People With Depression And Anxiety</p>
    <p class="hero-sub">Donate to our partner charity</p>
    <a class="btn-teal">Donate Now</a>
  </section>

  <section class="location">
    <h2 class="section-title">Current <span class="accent">Location</span></h2>
    <div class="rule"></div>
  </section>
  <div class="map" role="img" aria-label="Street map showing the riders' live GPS positions"></div>

  <section class="funds" role="group" aria-label="Fund raised progress over a mountain road landscape">
    <h2 class="section-title">Fund <span class="accent">Raised</span></h2>
    <div class="rule"></div>
    <div class="tag" style="left:20px;top:148px"><small>We Started</small><b>00 $</b></div>
    <div class="tag big" style="left:182px;top:114px"><small>Collected</small><b>10,588 $</b></div>
    <div class="tag" style="left:766px;top:148px"><small>Target</small><b>55,000 $</b></div>
    <div class="track">
      <div class="track-done"></div>
      <svg width="778" height="52" style="position:absolute;left:0;top:0">
        <g fill="#fff"><rect x="16" y="24" width="22" height="4"/><rect x="82" y="24" width="22" height="4"/><rect x="280" y="24" width="22" height="4"/><rect x="346" y="24" width="22" height="4"/><rect x="412" y="24" width="22" height="4"/><rect x="478" y="24" width="22" height="4"/><rect x="544" y="24" width="22" height="4"/><rect x="610" y="24" width="22" height="4"/><rect x="676" y="24" width="22" height="4"/><rect x="742" y="24" width="22" height="4"/></g>
        <circle cx="188" cy="26" r="16" fill="#e8246a"/><circle cx="188" cy="26" r="6" fill="#ffd200"/>
      </svg>
    </div>
    <a class="btn-pink">Donate Now</a>
  </section>

  <section class="journals">
    <h2 class="section-title">Recent Journals</h2>
    <div class="rule"></div>
    <article class="journal" style="left:58px">
      <div class="journal-photo" role="img" aria-label="Group of riders on a country road"><div class="date"><b>25</b><span>MAY<br>2016</span></div></div>
      <div class="count">1,256</div>
      <h3>Lorem Ipsum is simply dummy tex</h3>
      <p>When an unknown printer took a galley of type and scrambled it to make a type specimen book.</p>
      <a class="btn-black">Read More</a>
    </article>
    <article class="journal" style="left:484px">
      <div class="journal-photo" role="img" aria-label="Riders lined up on sport bikes"><div class="date"><b>25</b><span>MAY<br>2016</span></div></div>
      <div class="count">1,256</div>
      <h3>Lorem Ipsum is simply dummy tex</h3>
      <p>When an unknown printer took a galley of type and scrambled it to make a type specimen book.</p>
      <a class="btn-black">Read More</a>
    </article>
  </section>

  <section class="team">
    <div class="member" style="left:19px">
      <div class="avatar" role="img" aria-label="Portrait of rider Tom Barrett"></div>
      <h4>Tom Barrett</h4>
      <p>Donec sed odio dui. Etiam porta sem malesuada magna mollis euismod. Nullam id dolor id nibh ultricies.</p>
      <a class="btn-black">Read More</a>
    </div>
    <div class="member" style="left:310px">
      <div class="avatar" role="img" aria-label="Portrait of rider Daniel Greer"></div>
      <h4>Daniel Greer</h4>
      <p>Donec sed odio dui. Etiam porta sem malesuada magna mollis euismod. Nullam id dolor id nibh ultricies.</p>
      <a class="btn-black">Read More</a>
    </div>
    <div class="member" style="left:602px">
      <div class="avatar partner"><span>HarbourLight</span></div>
      <h4>HarbourLight</h4>
      <p>Donec sed odio dui. Etiam porta sem malesuada magna mollis euismod. Nullam id dolor id nibh ultricies.</p>
      <a class="btn-black">Visit</a>
    </div>
  </section>

  <section class="newsletter">
    Stay updated with latest news from
    <span class="field">Enter Your Email</span>
    <span class="subscribe">Subscribe</span>
  </section>

  <footer class="site-footer">
    Copyright © 2016 Coastline Ride . All Rights Reserved.
    <div class="payments"><em>We Accept :</em><span class="card">PayLink</span><span class="card">Versa</span><span class="card">Meridian</span><span class="card">Discovo</span></div>
  </footer>
</div>
</body>
</html>
```